Company Website Re-design for Software development consultancy

We would like our company website to be redesigned using our existing marketing collateral and website content as a guide

current site : www.brightkestrel.com.au

For the different pages types and content please base on the following site : https://www.quorvalabs.net/

We want a coded site - but will replace the content ourselves within the sections you provide to customise to our needs.

Target Market(s)

Medium to Large corporates needing software design and development services

Industry/Entity Type

Information Technology

Coding

Coded - Design and coding required

Number of Pages Required

5+ page

Font styles to use
Sans Serif

Colors
ec1f27
ffffff
000000

Requirements
Must have
• Align to colour scheme of existing collateral
• Include pages for the key areas of our busines - see : https://www.quorvalabs.net/
Nice to have
• image rotators - make the site interesting to the business visitor

```html
<!DOCTYPE html>
<html lang="en">
<head>
<meta charset="utf-8">
<title>Bright Kestrel — Building Software Better</title>
<link href="https://fonts.googleapis.com/css2?family=Poppins:wght@400;500;600;700&family=Open+Sans:wght@400;600&display=swap" rel="stylesheet">
<style>
:root{
  --red:#ec1f27;
  --red-dark:#b5121a;
  --black:#000;
  --ink:#1a1a1a;
  --white:#fff;
  --grey:#555;
  --light:#f4f4f4;
  --dark:#1c1c1c;
}
*{margin:0;padding:0;box-sizing:border-box}
html,body{width:1200px;height:4327px;overflow:hidden}
body{position:relative;background:var(--white);font-family:"Open Sans",Arial,sans-serif;color:var(--ink)}
.abs{position:absolute}
h1,h2,h3,h4,.heading{font-family:"Poppins",Arial,sans-serif}
.brand{display:flex;align-items:center;gap:12px;font-family:"Poppins",Arial,sans-serif;font-weight:700;text-transform:uppercase}
.brand-dot{border-radius:50%;display:inline-block}

/* header */
.site-header{top:0;left:0;width:1200px;height:150px}
.site-header .brand{position:absolute;left:88px;top:26px;font-size:38px;color:var(--black)}
.site-header .brand-dot{width:52px;height:52px;background:var(--red)}
.header-phone{position:absolute;left:800px;top:28px;font-size:22px;color:var(--black);display:flex;align-items:center;gap:8px}
.member-login{position:absolute;left:972px;top:24px;width:138px;height:34px;background:var(--black);color:var(--white);font-size:17px;display:flex;align-items:center;justify-content:center;border-right:8px solid var(--red)}
.main-nav{position:absolute;left:0;top:95px;width:1200px;height:56px}
.main-nav ul{position:absolute;right:92px;top:0;height:56px;display:flex;gap:44px;align-items:center;list-style:none;color:var(--white);font-size:19px}

/* hero */
.hero{top:150px;left:0;width:1200px;height:630px}
.hero-title{position:absolute;left:80px;top:205px;color:var(--white)}
.hero-title h1{font-size:74px;font-weight:700;line-height:1}
.hero-title p{font-family:"Poppins",Arial,sans-serif;font-size:38px;margin-top:22px}
.slider-dots{position:absolute;right:28px;top:240px;display:flex;flex-direction:column;gap:14px}
.slider-dots span{width:9px;height:9px;border-radius:50%;background:rgba(255,255,255,.6)}
.slider-dots span:first-child{background:var(--white)}

/* section headings */
.section-head{left:0;width:1200px;text-align:center}
.section-head h2{font-size:40px;font-weight:500;color:var(--black)}
.section-head p{font-size:23px;color:var(--ink);margin-top:4px}

/* faces */
.faces{top:950px;left:140px;width:920px;display:flex;justify-content:space-between}
.face{width:270px;text-align:center}
.face-icon{width:150px;height:140px;margin:0 auto;position:relative}
.face h3{font-size:27px;font-weight:500;margin-top:24px;color:var(--black)}
.face p{font-size:15px;line-height:1.55;color:var(--grey);margin-top:14px}
.face .more{margin-top:14px}

/* about */
.about{top:1370px;left:0;width:1200px;height:540px}
.about-content{position:absolute;left:140px;width:920px;top:125px;text-align:center;color:var(--white)}
.about-content h2{font-size:40px;font-weight:500}
.about-content p{font-size:15.5px;line-height:1.8;margin-top:20px}
.btn-light{display:inline-block;margin-top:26px;background:var(--white);color:var(--black);font-size:17px;padding:9px 36px;border-radius:22px}

/* what we do */
.services-emblem{left:425px;top:2118px;width:350px;height:350px}
.service{width:330px}
.service h4{font-size:21px;font-weight:500;color:var(--black)}
.service p{font-size:13.5px;line-height:1.6;color:var(--grey);margin-top:6px}
.service.left{left:188px;padding-left:0}
.service.right{text-align:right;left:680px}
.svc-icon{width:48px;height:48px}

/* contact */
.contact{top:2576px;left:0;width:1200px;height:560px}
.contact h2{position:absolute;top:140px;width:1200px;text-align:center;color:var(--white);font-size:40px;font-weight:500}
.field{position:absolute;height:52px;border:1.5px solid rgba(255,255,255,.85);color:var(--white);font-size:18px;padding:14px 18px}
.btn-submit{position:absolute;left:866px;top:395px;width:115px;height:40px;border-radius:20px;background:var(--white);color:var(--black);font-size:18px;display:flex;align-items:center;justify-content:center}

/* team */
.team-intro{left:160px;top:3300px;width:880px;text-align:center;font-size:18px;line-height:1.75;color:var(--ink)}
.team-card{top:3482px;width:312px;height:306px;background:var(--white);box-shadow:0 4px 16px rgba(0,0,0,.18);text-align:center;padding-top:100px}
.avatar{position:absolute;left:89px;top:-60px;width:134px;height:134px;border-radius:50%;border:4px solid var(--white);box-shadow:0 2px 8px rgba(0,0,0,.2)}
.team-card h4{font-size:20px;font-weight:500;color:var(--black);margin-top:4px}
.team-card .role{font-size:14px;color:var(--red);text-transform:uppercase;letter-spacing:.5px;margin-top:2px}
.team-card p{font-size:14px;line-height:1.65;color:var(--grey);margin:14px 32px 0}
.socials{display:flex;justify-content:center;gap:12px;margin-top:16px}
.socials span{width:28px;height:28px;border-radius:50%;border:1.5px solid #999}
.socials span:last-child{border-color:var(--red)}
.carousel-arrow{top:3610px;width:50px;height:50px;border-radius:50%;background:var(--white);box-shadow:0 2px 8px rgba(0,0,0,.2)}

/* footer */
.site-footer{top:3930px;left:0;width:1200px;height:397px}
.site-footer .brand{position:absolute;left:88px;top:182px;font-size:34px;color:var(--white)}
.site-footer .brand-dot{width:44px;height:44px;border:3px solid var(--white)}
.foot-col{position:absolute;top:136px;color:var(--white)}
.foot-col h5{font-family:"Poppins",Arial,sans-serif;font-weight:400;font-size:16px;letter-spacing:.5px;text-transform:uppercase;margin-bottom:20px}
.foot-col ul{list-style:none;font-size:13.5px;line-height:2}
.foot-col li::before{content:"› ";}
.contact-list{font-size:13.5px;line-height:1.6}
.contact-list div{display:flex;gap:14px;margin-bottom:14px}
.contact-list svg{flex:none;margin-top:2px}
.social-row{display:flex;gap:14px}
.social-row span{width:26px;height:26px;border-radius:4px;background:var(--white)}
.footer-rule{position:absolute;left:88px;top:330px;width:1024px;height:1px;background:#333}
.copyright{position:absolute;top:350px;width:1200px;text-align:center;color:var(--white);font-size:13px}
</style>
</head>
<body>

<header class="abs site-header">
  <div class="brand"><span class="brand-dot"></span>Bright Kestrel</div>
  <div class="header-phone">
    <svg width="20" height="20" viewBox="0 0 24 24"><path fill="#ec1f27" d="M6.6 10.8a15 15 0 0 0 6.6 6.6l2.2-2.2c.3-.3.7-.4 1-.2 1.1.4 2.3.6 3.6.6.6 0 1 .4 1 1V20c0 .6-.4 1-1 1A17 17 0 0 1 3 4c0-.6.4-1 1-1h3.5c.6 0 1 .4 1 1 0 1.3.2 2.5.6 3.6.1.3 0 .7-.2 1z"/></svg>
    0865550142
  </div>
  <div class="member-login">Member login</div>
  <nav class="main-nav">
    <svg class="abs" width="1200" height="56" viewBox="0 0 1200 56" style="left:0;top:0"><polygon points="70,0 1200,0 1200,56 0,56 0,28" fill="#ec1f27"/></svg>
    <ul><li>Home</li><li>About us</li><li>Services</li><li>Projects</li><li>News</li><li>Contact us</li></ul>
  </nav>
</header>

<section class="abs hero">
  <svg width="1200" height="630" viewBox="0 0 1200 630" class="abs" style="left:0;top:0">
    <defs>
      <radialGradient id="heroGlow" cx="0.68" cy="0.4" r="0.6">
        <stop offset="0" stop-color="#5fb4ff"/>
        <stop offset="0.35" stop-color="#1b4f8c"/>
        <stop offset="1" stop-color="#07101f"/>
      </radialGradient>
    </defs>
    <rect width="1200" height="630" fill="url(#heroGlow)" role="img" aria-label="Photo of a hand holding a glowing digital globe above a city skyline"/>
    <polygon points="0,560 1200,490 1200,630 0,630" fill="#ec1f27"/>
    <polygon points="0,600 1200,530 1200,630 0,630" fill="#fff"/>
  </svg>
  <div class="hero-title"><h1>BRIGHT KESTREL</h1><p>Building Software Better</p></div>
  <div class="slider-dots"><span></span><span></span><span></span><span></span></div>
</section>

<div class="abs section-head" style="top:855px">
  <h2>The Three Faces of Bright Kestrel</h2>
  <p>We are all about building software better.</p>
</div>

<div class="abs faces">
  <div class="face">
    <div class="face-icon">
      <svg width="150" height="140" viewBox="0 0 150 140"><polygon points="10,0 140,0 75,70" fill="#f7c7c9"/><rect x="30" y="30" width="90" height="100" rx="10" fill="#222" role="img" aria-label="Line icon of a team meeting around a presentation"/></svg>
    </div>
    <h3>Consulting</h3>
    <p>The point of using Lorem Ipsum is that it has a more-or-less normal distribution of letters, as opposed</p>
    <div class="more"><svg width="20" height="18" viewBox="0 0 20 18"><path d="M3 2l7 6 7-6M3 9l7 6 7-6" stroke="#000" stroke-width="2.4" fill="none"/></svg></div>
  </div>
  <div class="face">
    <div class="face-icon">
      <svg width="150" height="140" viewBox="0 0 150 140"><polygon points="10,0 140,0 75,70" fill="#f7c7c9"/><rect x="30" y="30" width="90" height="100" rx="10" fill="#222" role="img" aria-label="Line icon of hands holding a gear with a lightbulb"/></svg>
    </div>
    <h3>Projects</h3>
    <p>The point of using Lorem Ipsum is that it has a more-or-less normal distribution of letters, as opposed</p>
    <div class="more"><svg width="20" height="18" viewBox="0 0 20 18"><path d="M3 2l7 6 7-6M3 9l7 6 7-6" stroke="#000" stroke-width="2.4" fill="none"/></svg></div>
  </div>
  <div class="face">
    <div class="face-icon">
      <svg width="150" height="140" viewBox="0 0 150 140"><polygon points="10,0 140,0 75,70" fill="#f7c7c9"/><rect x="30" y="30" width="90" height="100" rx="10" fill="#222" role="img" aria-label="Line icon of a computer dashboard with a gauge"/></svg>
    </div>
    <h3>Impress</h3>
    <p>The point of using Lorem Ipsum is that it has a more-or-less normal distribution of letters, as opposed</p>
    <div class="more"><svg width="20" height="18" viewBox="0 0 20 18"><path d="M3 2l7 6 7-6M3 9l7 6 7-6" stroke="#000" stroke-width="2.4" fill="none"/></svg></div>
  </div>
</div>

<section class="abs about">
  <svg width="1200" height="540" viewBox="0 0 1200 540" class="abs" style="left:0;top:0">
    <rect y="0" width="1200" height="540" fill="#1f1f1f" role="img" aria-label="Dark photo of an office workspace"/>
    <polygon points="0,0 1200,0 1200,0 760,0" fill="#fff"/>
    <polygon points="780,40 1200,0 1200,95" fill="#ec1f27"/>
    <polygon points="780,40 1200,0 1200,0 0,0 0,40" fill="#fff"/>
    <polygon points="0,440 0,540 1200,540 1200,470 " fill="#fff"/>
    <polygon points="0,440 520,475 0,540" fill="#ec1f27"/>
  </svg>
  <div class="about-content">
    <h2>About us</h2>
    <p>It is a long established fact that a reader will be distracted by the readable content of a page when looking at its layout. The point of using Lorem Ipsum is that it has a more-or-less normal distribution of letters, as opposed to using 'Content here, content here', making it look like readable English. Many desktop publishing packages and web page editors now use Lorem Ipsum as their default model text, and a search for 'lorem ipsum' will uncover many web sites still in their infancy The point of using Lorem Ipsum is that it has a more-or-less normal distribution of letters, as opposed to using</p>
    <span class="btn-light">Read More</span>
  </div>
</section>

<div class="abs section-head" style="top:1985px">
  <h2>What We Do</h2>
  <p>Neque porro quisquam est qui dolorem</p>
</div>

<svg class="abs services-emblem" viewBox="0 0 350 350">
  <circle cx="175" cy="175" r="172" fill="#fff" stroke="#e3e3e3" stroke-width="2"/>
  <circle cx="175" cy="175" r="142" fill="none" stroke="#ec1f27" stroke-width="12"/>
  <circle cx="175" cy="175" r="112" fill="#ec1f27" role="img" aria-label="Company emblem placeholder"/>
</svg>

<div class="abs service left" style="top:2168px;left:126px">
  <svg class="abs svc-icon" viewBox="0 0 48 48" style="left:0;top:2px"><rect x="3" y="8" width="42" height="26" fill="none" stroke="#ec1f27" stroke-width="2"/><path d="M18 42h12M24 34v8" stroke="#ec1f27" stroke-width="2"/></svg>
  <div style="margin-left:62px"><h4>Noque porro</h4><p>Duis aute irure dolor<br>in reprehenderit in voluptata.<br>Excepteur sint occaecat.</p></div>
</div>
<div class="abs service left" style="top:2328px;left:126px">
  <svg class="abs svc-icon" viewBox="0 0 48 48" style="left:0;top:2px"><rect x="12" y="3" width="24" height="42" rx="3" fill="none" stroke="#ec1f27" stroke-width="2"/><path d="M20 39h8" stroke="#ec1f27" stroke-width="2"/></svg>
  <div style="margin-left:62px"><h4>Quisquam est</h4><p>Duis aute irure dolor<br>in reprehenderit in voluptata.<br>Excepteur sint occaecat.</p></div>
</div>
<div class="abs service right" style="top:2168px;left:740px">
  <svg class="abs svc-icon" viewBox="0 0 48 48" style="left:282px;top:2px"><circle cx="36" cy="10" r="6" fill="none" stroke="#ec1f27" stroke-width="2"/><circle cx="12" cy="24" r="6" fill="none" stroke="#ec1f27" stroke-width="2"/><circle cx="36" cy="38" r="6" fill="none" stroke="#ec1f27" stroke-width="2"/><path d="M17 21l14-8M17 27l14 8" stroke="#ec1f27" stroke-width="2"/></svg>
  <div style="margin-right:62px"><h4>Dolorem ipsum</h4><p>Duis aute irure dolor<br>in reprehenderit in voluptata.<br>Excepteur sint occaecat.</p></div>
</div>
<div class="abs service right" style="top:2328px;left:740px">
  <svg class="abs svc-icon" viewBox="0 0 48 48" style="left:282px;top:2px"><path d="M10 6h20l8 8v28H10z" fill="none" stroke="#ec1f27" stroke-width="2"/><path d="M16 20h16M16 27h16M16 34h10" stroke="#ec1f27" stroke-width="2"/></svg>
  <div style="margin-right:62px"><h4>porro quisquam</h4><p>Duis aute irure dolor<br>in reprehenderit in voluptata.<br>Excepteur sint occaecat.</p></div>
</div>

<section class="abs contact">
  <svg width="1200" height="560" viewBox="0 0 1200 560" class="abs" style="left:0;top:0">
    <defs>
      <linearGradient id="contactRed" x1="0" y1="0" x2="1" y2="1">
        <stop offset="0" stop-color="#ec1f27"/>
        <stop offset="1" stop-color="#9e0d14"/>
      </linearGradient>
    </defs>
    <rect width="1200" height="560" fill="url(#contactRed)" role="img" aria-label="Red tinted photo of an office team"/>
    <polygon points="0,0 1200,0 1200,0 0,90" fill="#111"/>
    <polygon points="0,0 1200,0 0,0" fill="#fff"/>
    <polygon points="1200,0 1200,60 700,0" fill="#111"/>
    <polygon points="0,470 1200,520 1200,560 0,560" fill="#111"/>
    <polygon points="0,520 1200,560 0,560" fill="#fff"/>
  </svg>
  <h2>Contact us</h2>
  <div class="field" style="left:216px;top:237px;width:375px">Name</div>
  <div class="field" style="left:606px;top:237px;width:375px">Email id</div>
  <div class="field" style="left:216px;top:318px;width:765px">Message</div>
  <div class="btn-submit">Submit</div>
</section>

<div class="abs section-head" style="top:3230px"><h2>Meet our leadership team</h2></div>
<p class="abs team-intro">Between just the partners, we have more than 60 years of software development experience. We combine a solid knowledge of computer science with a practical, pragmatic approach to delivering software.</p>

<svg class="abs carousel-arrow" viewBox="0 0 50 50" style="left:45px"><path d="M29 16l-9 9 9 9" stroke="#777" stroke-width="2" fill="none"/></svg>
<svg class="abs carousel-arrow" viewBox="0 0 50 50" style="left:1110px"><path d="M21 16l9 9-9 9" stroke="#777" stroke-width="2" fill="none"/></svg>

<div class="abs team-card" style="left:110px">
  <div class="avatar" style="background:#c9c9c9" role="img" aria-label="Portrait photo of Liam Fenwick"></div>
  <h4>Liam Fenwick</h4><div class="role">Partner</div>
  <p>It is a long established fact that a reader will be distracted by the readable content of a page</p>
  <div class="socials"><span></span><span></span><span></span></div>
</div>
<div class="abs team-card" style="left:447px">
  <div class="avatar" style="background:#bdbdbd" role="img" aria-label="Portrait photo of Marcus Hale"></div>
  <h4>Marcus Hale</h4><div class="role">Partner</div>
  <p>It is a long established fact that a reader will be distracted by the readable content of a page when</p>
  <div class="socials"><span></span><span></span><span></span></div>
</div>
<div class="abs team-card" style="left:785px">
  <div class="avatar" style="background:#c4cfc6" role="img" aria-label="Portrait photo of Owen Pryce"></div>
  <h4>Owen Pryce</h4><div class="role">Partner</div>
  <p>It is a long established fact that a reader will be distracted by the readable content of a page</p>
  <div class="socials"><span></span><span></span><span></span></div>
</div>

<footer class="abs site-footer">
  <svg width="1200" height="397" viewBox="0 0 1200 397" class="abs" style="left:0;top:0">
    <polygon points="0,0 1200,40 1200,397 0,397" fill="#000"/>
    <polygon points="0,0 1200,40 1200,70 0,75" fill="#ec1f27"/>
    <polygon points="0,75 1200,70 1200,397 0,397" fill="#000"/>
  </svg>
  <div class="brand"><span class="brand-dot"></span>Bright Kestrel</div>
  <div class="foot-col" style="left:413px">
    <h5>Information</h5>
    <ul><li>Privacy Policy</li><li>Your Account</li><li>Advanced Search</li><li>Contact Us</li></ul>
  </div>
  <div class="foot-col" style="left:640px">
    <h5>Contact us</h5>
    <div class="contact-list">
      <div><svg width="14" height="18" viewBox="0 0 14 18"><path d="M7 0a7 7 0 0 0-7 7c0 5 7 11 7 11s7-6 7-11a7 7 0 0 0-7-7zm0 10a3 3 0 1 1 0-6 3 3 0 0 1 0 6z" fill="#ec1f27"/></svg><span>42 - 44 Harbour Ln, Sydney 2000<br>Australia</span></div>
      <div><svg width="14" height="16" viewBox="0 0 24 24"><path fill="#ec1f27" d="M6.6 10.8a15 15 0 0 0 6.6 6.6l2.2-2.2c.3-.3.7-.4 1-.2 1.1.4 2.3.6 3.6.6.6 0 1 .4 1 1V20c0 .6-.4 1-1 1A17 17 0 0 1 3 4c0-.6.4-1 1-1h3.5c.6 0 1 .4 1 1 0 1.3.2 2.5.6 3.6.1.3 0 .7-.2 1z"/></svg><span>0155 210 4478</span></div>
      <div><svg width="16" height="14" viewBox="0 0 16 12"><rect width="16" height="12" fill="#ec1f27"/><path d="M0 0l8 6 8-6" stroke="#000" fill="none"/></svg><span>info@brightkestrel.com.au</span></div>
    </div>
  </div>
  <div class="foot-col" style="left:935px">
    <h5>Follow us out there</h5>
    <div class="social-row"><span></span><span></span><span></span><span></span></div>
  </div>
  <div class="footer-rule"></div>
  <div class="copyright">Copyright © 2018 All Rights Reserved</div>
</footer>

</body>
</html>
```